Locksmith SmartPhone Web Design Project

I am a locksmith and focus on customers that use their smart phones to find me. I have a static web page that I created myself but it is horrible. See for yourself at www.brackenlocksmiths.com.au

I want a cross-platform static site that simply shows the information and with the ability to change minor items like pricing. I want it to be compelling in its look and feel (not overwhelming) but simple. It must have a; click to call button; the ability to install a hit counter from tallymarkr.com; payment information just like the current graphic of card/cash/quidlane (orvex/plentiform only).

This will be hosted on my own server.
Updates

Hello Designers,

I have updated the brief in the must have and nice to have fields.

Thank you all,

Trent.

Hello to all Designers,

There is about 9 days left before the deadline. The overall level of competition is extremely high and I would like to thank all the designers who have submitted so far, 27 submissions in total so far. Excellent work.

If you have submitted already and wish to provide new designs, I am keen to see them. 

Hi guys, time is almost up. Please submit any new designs that you may have. The quality has been excellent so far.

Trent.

Target Market(s)

People who are locked out of their house/shop/office etc.

Industry/Entity Type

Locksmith

Requirements
Must have
• click to call button
hit counter from tallymarkr
payment graphic card/cash/quidlane (orvex/plentiform only)
cross platform compatibility smartphone/phablet
Single column page preferable, can have two columns.
Nice to have
• When the page loads regardless of the mobile device, all info should be presented. In other words no vertical or horizontal scroll bars.
Should not have
• hidden code, advertising, credits etc

```html
<!DOCTYPE html>
<html lang="en">
<head>
<meta charset="utf-8">
<title>Bracken Locksmiths – Lockout Service</title>
<link rel="stylesheet" href="https://fonts.googleapis.com/css2?family=Federo&family=Jost:wght@400;500;600;700&family=Poiret+One&display=swap">
<style>
:root{
  --page:#2f3030;
  --page-edge:#262727;
  --card:#c8d5ca;
  --card-line:#b6c6b9;
  --frame:#2a2a2a;
  --white:#ffffff;
  --ink:#111111;
  --green-text:#4f7460;
  --gold:#8c7232;
  --gold-line:#b59a5c;
  --call-top:#a6d43a;
  --call-bottom:#6c9f14;
  --call-ring:#1c1d1d;
  --yes:#a9d8b8;
  --badge:#0c0c0c;
}
*{box-sizing:border-box;margin:0;padding:0}
html,body{width:800px;height:1200px;overflow:hidden;background:var(--page)}
.screen{position:relative;width:800px;height:1200px;background:var(--page);font-family:"Jost",sans-serif;color:var(--white)}
.pattern-card{position:absolute;left:20px;top:40px;width:760px;height:866px;border-radius:28px;background:var(--card);box-shadow:0 3px 8px rgba(0,0,0,.5)}
.logo-frame{position:absolute;left:122px;top:75px;width:568px;height:163px;background:var(--frame);border-radius:14px;padding:12px}
.logo-plate{width:100%;height:100%;background:var(--white);border-radius:4px;text-align:center;padding-top:16px}
.logo-name{font-family:"Poiret One",sans-serif;font-size:74px;line-height:74px;letter-spacing:14px;color:var(--ink);padding-left:14px}
.logo-rule{width:488px;height:2px;background:var(--ink);margin:4px auto 6px}
.logo-sub{font-family:"Jost",sans-serif;font-size:29px;letter-spacing:6px;color:var(--green-text)}
.offer-banner{position:absolute;left:0;top:362px;width:800px;height:307px;background:linear-gradient(#ffffff 0%,#f2f2f2 55%,#d9d9d9 100%);box-shadow:0 6px 12px rgba(0,0,0,.45);text-align:center}
.offer-title{font-family:"Federo",sans-serif;font-size:74px;color:var(--green-text);margin-top:34px;line-height:80px}
.offer-price{font-family:"Jost",sans-serif;font-weight:500;font-size:35px;letter-spacing:1px;color:var(--gold);margin-top:22px}
.offer-divider{position:relative;width:680px;height:20px;margin:14px auto 0}
.offer-divider::before,.offer-divider::after{content:"";position:absolute;top:9px;width:310px;height:2px;background:linear-gradient(90deg,transparent,var(--gold-line))}
.offer-divider::before{left:0}
.offer-divider::after{right:0;transform:scaleX(-1)}
.divider-dot{position:absolute;left:334px;top:4px;width:12px;height:12px;background:var(--gold-line);transform:rotate(45deg)}
.offer-service{font-family:"Federo",sans-serif;font-size:36px;color:var(--green-text);margin-top:12px}
.payment-row{position:absolute;top:746px;left:118px;display:flex;gap:26px}
.pay-tile{width:122px;height:78px;border:3px solid #4e6b5a;background:var(--white);display:flex;align-items:center;justify-content:center;font-family:"Jost",sans-serif;font-weight:600;font-size:21px;color:#24366e}
.pay-tile.cash{background:linear-gradient(135deg,#c7c9a6,#8fb0a4 50%,#d9c7a0);}
.call-ring{position:absolute;left:16px;top:926px;width:768px;height:96px;border-radius:26px;background:var(--call-ring)}
.call-button{position:absolute;left:24px;top:934px;width:752px;height:80px;border-radius:20px;background:linear-gradient(var(--call-top),var(--call-bottom));display:flex;align-items:center;justify-content:center;color:var(--ink);text-decoration:none;box-shadow:inset 0 2px 0 rgba(255,255,255,.35)}
.call-word{font-size:37px;font-weight:400;letter-spacing:1px}
.call-number{font-size:56px;font-weight:600;margin:0 42px 0 40px;letter-spacing:1px}
.status{position:absolute;top:1038px;width:800px;text-align:center;font-size:35px;font-weight:600;letter-spacing:.5px}
.status-yes{color:var(--yes);margin-left:8px}
.clock{position:absolute;top:1092px;left:157px;font-size:28px;font-weight:400}
.footer-ids{position:absolute;top:1152px;left:28px;font-size:21px;word-spacing:2px}
.footer-ids span+span{margin-left:22px}
.hit-badge{position:absolute;left:660px;top:1144px;width:113px;height:37px;background:var(--badge);border-radius:3px;font-size:20px;display:flex;align-items:center;justify-content:center}
</style>
</head>
<body>
<main class="screen">
  <div class="pattern-card" role="img" aria-label="Pale green geometric lattice background"></div>

  <div class="logo-frame">
    <div class="logo-plate">
      <div class="logo-name">BRACKEN</div>
      <div class="logo-rule"></div>
      <div class="logo-sub">LOCKSMITHS</div>
    </div>
  </div>

  <section class="offer-banner">
    <h1 class="offer-title">Locked Out?</h1>
    <p class="offer-price">$150 GETS YOU IN. EASY!</p>
    <div class="offer-divider"><span class="divider-dot"></span></div>
    <p class="offer-service">Locksmith Lockout Service</p>
  </section>

  <div class="payment-row">
    <div class="pay-tile">plentiform</div>
    <div class="pay-tile">orvex</div>
    <div class="pay-tile cash" role="img" aria-label="Fanned Australian banknotes for cash payment"></div>
    <div class="pay-tile">quidlane</div>
  </div>

  <div class="call-ring"></div>
  <a class="call-button" href="tel:0491570156">
    <span class="call-word">CALL</span>
    <span class="call-number">0491570156</span>
    <span class="call-word">NOW</span>
  </a>

  <p class="status">LOCKSMITH AVAILABLE?<span class="status-yes">YES</span></p>
  <p class="clock">Time Now 2:27 PM</p>

  <p class="footer-ids"><span>ABN: 51824753556</span><span>Master License: 409182736</span></p>
  <div class="hit-badge">1802 Hits</div>
</main>
</body>
</html>
```